Application page web design and internal pages

Create a web site where home
Page looks like an application screen for a mobile phone

Use bold icons and colors with images that have round edges

PorlenPurse Apps is name of page

Search bar at the top

Use colors from Vextaro.org for background

Price of ZORBS in top right corner (https://www.quelvix.example/trade/en-US?symbol=ZORBS_USDT&layout=basic&theme=dark)

Pages within each app should be the same color as the icon

Use the following as app icons on the page:
Key
Icon name: first screen; second screen (text)

⁃ Balances: enter pin; display balances (Your account can hold multiple currency denominations. Your balances are: ZORBS 1234567890)
⁃ Transactions: enter pin; display transactions (Your last 5 payments are ZORBS 10 from Vextaro)
⁃ Send Money: enter phone number, enter amount, send button; display message
⁃ Create Account: choose country code, enter phone number, create button; enter pin; display message ( (phone number) will be notified when their account has been created)
⁃ My Wallet Address: enter pin; display public key (IMPORTANT Send only STELLAR blockchain tokens to this deposit address: GDXQ7PLM2ZNVA9TRK4WSEY8HCBUJ6FOGDLIXP3QM5RTVKNAWZEHOBCYS)
⁃ Private Message: enter phone number, enter message, choose image, send button; enter pin; display message ( (phone number) will be notified when their message has been created)
⁃ Buy Cryptocurrency: drop drown menu of cryptocurrency to purchase (Bitcoin/Ethereum/Stellar/ZORBS), Amount in USD field, amount in chosen cryptocurrency displayed, frequency drop down menu (once/daily/weekly/monthly), buy button; enter card information (name, card number, expiration date, cvv, billing address, zip code), confirm buy button, transactions will appear on your billing statement as VEXTARO; enter pin screen; display message (You will be notified when your coin is received)
⁃ NFTs: upload image, title, description, link media, create NFT button; enter pin screen; display message (You will be notified when your NFT is created)
⁃ Earn: display message (Earn cryptocurrency doing what you do everyday, coming soon)
⁃ Files/Vault: display message (Storage for your photos, documents and more, coming soon)
⁃ Wealth: display message (Build wealth by working with a financial professional to get you to the next level), check box (I would like a financial professional to contact me about building wealth), contact me button; display message (A financial professional will contact you to achieve your financial goals)
⁃ Education: display message (Learn more about everything, coming soon)
⁃ News: display message (News from around the world, coming soon)
⁃ FAQs: use FAQs from this link https://vextaro.example/faq
⁃ Contact Us: enter message, send button; display message (Thank you for reaching out. We will reply to your message in the order it was received. Your patience is appreciated. Blessings.)

Requirements
Must have
• Application home page that looks like the Home Screen of a mobile phone
Nice to have
• Colorful icons

```html
<!DOCTYPE html>
<html lang="en">
<head>
<meta charset="utf-8">
<title>PorlenPurse Apps – NFTs, Earn, Files/Vault</title>
<link rel="stylesheet" href="https://fonts.googleapis.com/css2?family=Roboto:wght@400;500;700;900&display=swap">
<style>
:root{
  --board:#bdbec0;
  --ink:#0b0b0f;
  --navy:#17173a;
  --white:#ffffff;
  --text:#2d2d35;
  --muted:#6d6f76;
  --line:#c9cbd1;
  --tile:#d8d9dc;
  --tile-icon:#66676c;
  --success:#3bcf74;
}
*{box-sizing:border-box;margin:0;padding:0}
html,body{width:1200px;height:1134px;overflow:hidden;background:var(--board)}
body{position:relative;font-family:'Roboto',Arial,sans-serif;color:var(--text)}
.board-title,.section-title{position:absolute;font-weight:900;color:var(--ink);font-size:31px;line-height:1;letter-spacing:0.2px}
.section-title.center{transform:translateX(-50%)}

.screen{position:absolute;width:203px;height:392px;background:var(--white);overflow:hidden}
.backdrop{position:absolute;left:0;top:0;width:203px;height:392px}
.brand{position:absolute;left:0;right:0;top:58px;text-align:center;color:var(--white);font-size:9.5px;font-weight:500;letter-spacing:1.6px;line-height:12px}
.ticker{position:absolute;left:42px;top:82px;width:119px;height:30px;background:var(--navy);color:var(--white);display:flex;align-items:center;justify-content:space-between;padding:0 12px;font-size:8px}
.search{position:absolute;left:20px;top:126px;width:162px;height:22px;background:var(--white);box-shadow:0 1px 4px rgba(0,0,0,.12);display:flex;align-items:center;justify-content:space-between;padding-left:7px;font-size:5px;color:var(--muted)}
.search-btn{width:20px;height:20px;margin-right:1px;background:var(--navy);border-radius:3px;display:flex;align-items:center;justify-content:center}
.menu{position:absolute;left:18px;top:172px;width:14px;height:11px}
.policy{position:absolute;left:0;right:0;top:361px;text-align:center;font-size:4.2px;color:var(--muted)}
.tabbar{position:absolute;left:0;right:0;bottom:0;height:19px;background:var(--navy);display:flex;align-items:center;justify-content:center}

.heading{position:absolute;left:0;right:0;text-align:center;font-weight:500;font-size:9px;color:var(--ink)}
.label{position:absolute;left:17px;font-size:7px;color:var(--muted)}
.field{position:absolute;left:18px;width:140px;height:24px;border:1px solid var(--line);border-radius:3px;background:var(--white);display:flex;align-items:center;justify-content:space-between;padding:0 8px;font-size:7px;color:var(--muted)}
.pill{position:absolute;height:20px;border-radius:10px;background:var(--navy);color:var(--white);font-size:7.5px;font-weight:700;display:flex;align-items:center;justify-content:center}
.note{position:absolute;left:0;right:0;text-align:center;font-size:7px;color:var(--text)}
.pin-slot{position:absolute;top:248px;width:20px;height:1px;background:var(--line)}
.tile{position:absolute;top:236px;width:58px;height:58px;background:var(--tile);display:flex;flex-direction:column;align-items:center;justify-content:center;gap:5px;font-size:7px;color:var(--text)}
</style>
</head>
<body>

<svg width="0" height="0" style="position:absolute" aria-hidden="true">
  <defs>
    <linearGradient id="header-fill" x1="0" y1="0" x2="0.55" y2="1">
      <stop offset="0" stop-color="#0f1c3b"/>
      <stop offset="0.45" stop-color="#12466b"/>
      <stop offset="1" stop-color="#1fa4bc"/>
    </linearGradient>
    <symbol id="header-shape" viewBox="0 0 203 392">
      <path d="M8,0 H203 V160 C192,112 165,86 108,82 C56,78 20,44 8,0 Z" fill="url(#header-fill)"/>
    </symbol>
    <symbol id="magnifier" viewBox="0 0 24 24">
      <circle cx="10.5" cy="10.5" r="6.5" fill="none" stroke="#fff" stroke-width="2"/>
      <path d="M15.5 15.5 L20 20" stroke="#fff" stroke-width="2" stroke-linecap="round"/>
    </symbol>
    <symbol id="burger" viewBox="0 0 14 11">
      <rect y="0" width="14" height="1.6" fill="#17173a"/>
      <rect y="4.7" width="14" height="1.6" fill="#17173a"/>
      <rect y="9.4" width="14" height="1.6" fill="#17173a"/>
    </symbol>
    <symbol id="home" viewBox="0 0 24 24">
      <path d="M12 3 L2 12 H5 V21 H10 V15 H14 V21 H19 V12 H22 Z" fill="#fff"/>
    </symbol>
  </defs>
</svg>

<h1 class="board-title" style="left:118px;top:42px">NFTS</h1>
<h2 class="section-title center" style="left:352px;top:110px">SCREEN 1</h2>
<h2 class="section-title center" style="left:742px;top:110px">SCREEN 2</h2>
<h2 class="section-title center" style="left:1010px;top:110px">SCREEN 3</h2>
<h2 class="section-title" style="left:116px;top:620px">EARN</h2>
<h2 class="section-title" style="left:376px;top:620px">FILES/VAULT</h2>

<!-- NFT form -->
<section class="screen" style="left:118px;top:169px">
  <svg class="backdrop"><use href="#header-shape"/></svg>
  <p class="brand">PORLENPURSE</p>
  <div class="ticker"><span>ZORBS &#8964;</span><span>$ 5.98 &nbsp;&#8593;</span></div>
  <div class="search"><span>Search Here</span><span class="search-btn"><svg width="12" height="12"><use href="#magnifier"/></svg></span></div>
  <svg class="menu"><use href="#burger"/></svg>
  <p class="heading" style="top:191px">NFTS</p>
  <p class="label" style="top:216px">Upload Image</p>
  <div class="field" style="top:230px"><span>Choose Your File</span>
    <svg width="8" height="10" viewBox="0 0 8 10"><path d="M0 0 H5.5 L8 2.5 V10 H0 Z" fill="#17173a"/><path d="M4 8 V4.5 M2.5 6 L4 4.5 L5.5 6" stroke="#fff" stroke-width="0.9" fill="none"/></svg>
  </div>
  <p class="label" style="top:264px">Title</p>
  <div class="field" style="top:278px"></div>
  <p class="label" style="top:312px">Description</p>
  <div class="field" style="top:326px"></div>
  <p class="policy">&copy;Vextaro Zero Liability Transaction Policy</p>
  <nav class="tabbar"><svg width="10" height="10"><use href="#home"/></svg></nav>
</section>

<!-- NFT link media -->
<section class="screen" style="left:379px;top:169px">
  <svg class="backdrop"><use href="#header-shape"/></svg>
  <p class="brand">PORLENPURSE</p>
  <div class="ticker"><span>ZORBS &#8964;</span><span>$ 5.98 &nbsp;&#8593;</span></div>
  <div class="search"><span>Search Here</span><span class="search-btn"><svg width="12" height="12"><use href="#magnifier"/></svg></span></div>
  <svg class="menu"><use href="#burger"/></svg>
  <p class="label" style="top:206px;left:29px">Link Media</p>
  <div class="field" style="top:222px;left:29px;width:142px"><span>Search Here</span>
    <svg width="8" height="8" viewBox="0 0 24 24"><circle cx="10.5" cy="10.5" r="7" fill="none" stroke="#17173a" stroke-width="2.6"/><path d="M15.5 15.5 L21 21" stroke="#17173a" stroke-width="2.6"/></svg>
  </div>
  <div class="pill" style="left:64px;top:256px;width:74px">CREATE &nbsp;NFT</div>
  <p class="policy">&copy;Vextaro Zero Liability Transaction Policy</p>
  <nav class="tabbar"><svg width="10" height="10"><use href="#home"/></svg></nav>
</section>

<!-- PIN -->
<section class="screen" style="left:638px;top:169px">
  <svg class="backdrop"><use href="#header-shape"/></svg>
  <p class="brand">PORLENPURSE</p>
  <div class="ticker"><span>ZORBS &#8964;</span><span>$ 5.98 &nbsp;&#8593;</span></div>
  <div class="search"><span>Search Here</span><span class="search-btn"><svg width="12" height="12"><use href="#magnifier"/></svg></span></div>
  <svg class="menu"><use href="#burger"/></svg>
  <p class="note" style="top:217px">Enter Your Pin Here</p>
  <span class="pin-slot" style="left:38px"></span>
  <span class="pin-slot" style="left:74px"></span>
  <span class="pin-slot" style="left:110px"></span>
  <span class="pin-slot" style="left:146px"></span>
  <div class="pill" style="left:65px;top:267px;width:74px">SEND</div>
  <p class="policy">&copy;Vextaro Zero Liability Transaction Policy</p>
  <nav class="tabbar"><svg width="10" height="10"><use href="#home"/></svg></nav>
</section>

<!-- Confirmation -->
<section class="screen" style="left:907px;top:169px">
  <svg class="backdrop"><use href="#header-shape"/></svg>
  <p class="brand">PORLENPURSE</p>
  <div class="ticker"><span>ZORBS &#8964;</span><span>$ 5.98 &nbsp;&#8593;</span></div>
  <div class="search"><span>Search Here</span><span class="search-btn"><svg width="12" height="12"><use href="#magnifier"/></svg></span></div>
  <svg class="menu"><use href="#burger"/></svg>
  <svg style="position:absolute;left:92px;top:212px" width="20" height="20" viewBox="0 0 20 20">
    <circle cx="10" cy="10" r="8.8" fill="none" stroke="var(--success)" stroke-width="1.4"/>
    <path d="M6 10.3 L8.8 13 L14 7.3" fill="none" stroke="var(--success)" stroke-width="1.4"/>
  </svg>
  <p class="note" style="top:243px">You will be notified when your NFT is created</p>
  <p class="policy">&copy;Vextaro Zero Liability Transaction Policy</p>
  <nav class="tabbar"><svg width="10" height="10"><use href="#home"/></svg></nav>
</section>

<!-- Earn -->
<section class="screen" style="left:118px;top:688px">
  <svg class="backdrop"><use href="#header-shape"/></svg>
  <p class="brand">PORLENPURSE</p>
  <div class="ticker"><span>ZORBS &#8964;</span><span>$ 5.98 &nbsp;&#8593;</span></div>
  <div class="search"><span>Search Here</span><span class="search-btn"><svg width="12" height="12"><use href="#magnifier"/></svg></span></div>
  <svg class="menu"><use href="#burger"/></svg>
  <p class="heading" style="top:216px">EARN</p>
  <p class="note" style="top:237px;font-size:7.3px">Earn cryptocurrency doing what you do everyday,</p>
  <p class="note" style="top:248px;font-weight:500;color:var(--ink)">coming soon</p>
  <p class="policy">&copy;Vextaro Zero Liability Transaction Policy</p>
  <nav class="tabbar"><svg width="10" height="10"><use href="#home"/></svg></nav>
</section>

<!-- Files / Vault -->
<section class="screen" style="left:379px;top:688px">
  <svg class="backdrop"><use href="#header-shape"/></svg>
  <p class="brand">PORLENPURSE</p>
  <div class="ticker"><span>ZORBS &#8964;</span><span>$ 5.98 &nbsp;&#8593;</span></div>
  <div class="search"><span>Search Here</span><span class="search-btn"><svg width="12" height="12"><use href="#magnifier"/></svg></span></div>
  <svg class="menu"><use href="#burger"/></svg>
  <p class="heading" style="top:193px">FILES/VAULT</p>
  <p class="note" style="top:210px;font-size:8.5px;color:var(--ink)">Storage For Your</p>
  <div class="tile" style="left:24px">
    <svg width="26" height="22" viewBox="0 0 26 22"><rect x="5" y="1" width="20" height="16" rx="1.5" fill="var(--tile-icon)"/><rect x="1" y="5" width="20" height="16" rx="1.5" fill="none" stroke="var(--tile-icon)" stroke-width="1.5"/><circle cx="10" cy="6" r="2" fill="var(--tile)"/><path d="M7 15 L12 9 L16 13 L19 10 L23 15 Z" fill="var(--tile)"/></svg>
    <span>Photos</span>
  </div>
  <div class="tile" style="left:95px">
    <svg width="18" height="22" viewBox="0 0 18 22"><path d="M0 0 H12 L18 6 V22 H0 Z" fill="var(--tile-icon)"/><path d="M4 10 H14 M4 13.5 H14 M4 17 H14" stroke="var(--tile)" stroke-width="1.3"/></svg>
    <span>Documents</span>
  </div>
  <p class="note" style="top:310px;font-weight:500;color:var(--ink)">More Coming Soon</p>
  <p class="policy">&copy;Vextaro Zero Liability Transaction Policy</p>
  <nav class="tabbar"><svg width="10" height="10"><use href="#home"/></svg></nav>
</section>

</body>
</html>
```